Spring Detox sale graphics for social media

You MUST read the Brief in the WORD document and follow the instructions there. I want to create 10 social media graphics (new Instagram size 4:5 (1080 x 1350 pixels) focusing on our Mother’s Day Spring Detox Sale graphics, using any of the pics attached. Use the attached pics, NO RANDOM STOCK PHOTOGRAPHY. For the color scheme of the graphics, they should all be complementary to the product colors or feel like Spring time.

Target Market(s)

primarily women

Requirements
Must have
• the photos and text attached

```html
<!DOCTYPE html>
<html lang="en">
<head>
<meta charset="utf-8">
<title>Mother's Day Spring Detox Sale — Social Set</title>
<link rel="stylesheet" href="https://fonts.googleapis.com/css2?family=League+Gothic&family=Source+Sans+3:wght@600;700&display=swap">
<style>
  :root {
    --bg: #000000;
    --ink: #ffffff;
    --forest: #265e2e;
    --orchid: #a93597;
    --plum: #7a3a58;
    --berry: #cc1f79;
    --poppy: #ff0022;
    --pine: #106a55;
    --midnight: #1e0a4c;
    --cobalt: #030d82;
    --badge: #ff1dce;
    --bottle-light: #e9e6ea;
    --bottle-shade: #bdb6c2;
  }
  * { margin: 0; padding: 0; box-sizing: border-box; }
  html, body { width: 1200px; height: 2652px; overflow: hidden; background: var(--bg); }
  .canvas { position: relative; width: 1200px; height: 2652px; }

  .tile { position: absolute; width: 345px; height: 430px; overflow: hidden; color: var(--ink); }
  .col-a { left: 248px; } .col-b { left: 607px; }
  .row-1 { top: 215px; } .row-2 { top: 663px; } .row-3 { top: 1109px; } .row-4 { top: 1557px; } .row-5 { top: 2003px; }

  .line { position: absolute; font-family: "League Gothic", "Oswald", sans-serif; line-height: 0.9; letter-spacing: 0.02em; white-space: nowrap; }
  .center { left: 0; width: 100%; text-align: center; }
  .sans { font-family: "Source Sans 3", "Helvetica Neue", sans-serif; font-weight: 700; line-height: 1; letter-spacing: 0; }

  .price { --n: 100px; position: absolute; display: flex; align-items: flex-start; font-family: "League Gothic", "Oswald", sans-serif; line-height: 0.85; white-space: nowrap; }
  .price.center-price { left: 0; width: 100%; justify-content: center; }
  .price .num { font-size: var(--n); letter-spacing: 0.02em; }
  .price .suffix { display: flex; flex-direction: column; margin-left: 3px; padding-top: calc(var(--n) * 0.04); }
  .price .pct { font-size: calc(var(--n) * 0.44); }
  .price .off { font-size: calc(var(--n) * 0.38); }
  .price .tag { font-family: "Source Sans 3", sans-serif; font-weight: 700; font-size: 19px; margin-left: 10px; align-self: center; }

  .product-shot { position: absolute; border-radius: 8px;
    background: linear-gradient(180deg, var(--bottle-light) 0%, var(--bottle-shade) 100%); opacity: 0.9; }

  .badge { position: absolute; width: 106px; height: 106px; border-radius: 50%; background: var(--badge); }

  .forest { background: var(--forest); } .orchid { background: var(--orchid); } .plum { background: var(--plum); }
  .berry { background: var(--berry); } .poppy { background: var(--poppy); } .pine { background: var(--pine); }
  .midnight { background: var(--midnight); } .cobalt { background: var(--cobalt); }
</style>
</head>
<body>
<main class="canvas">

  <!-- Post 1 -->
  <section class="tile forest col-a row-1">
    <div class="line" style="left:42px;top:55px;font-size:58px;">MOTHER’S DAY</div>
    <div class="line" style="left:40px;top:105px;font-size:122px;">SPRING</div>
    <div class="line" style="left:42px;top:209px;font-size:81px;">Detox Sale</div>
    <div class="price" style="left:40px;top:288px;--n:101px;">
      <span class="num">25</span>
      <span class="suffix"><span class="pct">%</span><span class="off">OFF</span></span>
      <span class="tag">Everything!</span>
    </div>
  </section>

  <!-- Post 2 -->
  <section class="tile orchid col-b row-1">
    <div class="product-shot" role="img" aria-label="Row of four white supplement bottles" style="left:43px;top:9px;width:260px;height:110px;"></div>
    <div class="price" style="left:66px;top:135px;--n:89px;">
      <span class="num">25</span>
      <span class="suffix"><span class="pct">%</span><span class="off">OFF</span></span>
    </div>
    <div class="line" style="left:66px;top:216px;font-size:57px;">Mother’s Day</div>
    <div class="line" style="left:64px;top:258px;font-size:105px;">Spring</div>
    <div class="line" style="left:66px;top:356px;font-size:58px;">DETOX SALE</div>
  </section>

  <!-- Post 3 -->
  <section class="tile plum col-a row-2">
    <div class="price center-price" style="top:58px;--n:126px;">
      <span class="num">25</span>
      <span class="suffix"><span class="pct">%</span><span class="off">OFF</span></span>
    </div>
    <div class="line center sans" style="top:168px;font-size:31px;font-weight:600;">All Supplements</div>
    <div class="line center" style="top:208px;font-size:119px;">SPRING</div>
    <div class="line center" style="top:311px;font-size:72px;">DETOX SALE</div>
  </section>

  <!-- Post 4 -->
  <section class="tile berry col-b row-2">
    <div class="price" style="left:12px;top:30px;--n:104px;">
      <span class="num">25</span>
      <span class="suffix"><span class="pct">%</span><span class="off">OFF</span></span>
    </div>
    <div class="product-shot" role="img" aria-label="Four white supplement bottles in a staggered row" style="left:175px;top:35px;width:156px;height:93px;"></div>
    <div class="line" style="left:62px;top:145px;font-size:52px;">SPRING DETOX</div>
    <div class="line" style="left:59px;top:185px;font-size:145px;">SALE</div>
    <div class="line sans" style="left:62px;top:312px;font-size:32px;letter-spacing:1px;">Spring&nbsp; Reset</div>
    <div class="line sans" style="left:62px;top:347px;font-size:28px;letter-spacing:1px;">Summer&nbsp; Ready</div>
  </section>

  <!-- Post 5 -->
  <section class="tile poppy col-a row-3">
    <div class="price" style="left:48px;top:64px;--n:96px;">
      <span class="num">25</span>
      <span class="suffix"><span class="pct">%</span><span class="off">OFF</span></span>
      <span class="tag" style="font-size:18px;">Everything!</span>
    </div>
    <div class="line" style="left:50px;top:158px;font-size:52px;">MOTHER’S DAY</div>
    <div class="line" style="left:49px;top:206px;font-size:110px;">SPRING</div>
    <div class="line" style="left:50px;top:296px;font-size:66px;">DETOX SALE</div>
  </section>

  <!-- Post 6 -->
  <section class="tile pine col-b row-3">
    <div class="price center-price" style="top:45px;--n:85px;">
      <span class="num">25</span>
      <span class="suffix"><span class="pct">%</span><span class="off">OFF</span></span>
    </div>
    <div class="line center" style="top:121px;font-size:49px;">MOTHER’S DAY</div>
    <div class="line center" style="top:159px;font-size:130px;">SALE</div>
    <div class="line center" style="top:268px;font-size:50px;">FEEL AMAZING</div>
    <div class="line center" style="top:308px;font-size:95px;">AGAIN!</div>
  </section>

  <!-- Post 7 -->
  <section class="tile orchid col-a row-4">
    <div class="price center-price" style="top:56px;--n:93px;">
      <span class="num">25</span>
      <span class="suffix"><span class="pct">%</span><span class="off">OFF</span></span>
    </div>
    <div class="line center" style="top:139px;font-size:72px;">MOTHER’S</div>
    <div class="line center" style="top:198px;font-size:75px;">DAY SALE</div>
    <div class="line center" style="top:255px;font-size:87px;">REFRESH</div>
    <div class="line center" style="top:322px;font-size:66px;">YOUR BODY</div>
  </section>

  <!-- Post 8 -->
  <section class="tile orchid col-b row-4">
    <div class="badge" style="left:203px;top:33px;"></div>
    <div class="price" style="left:216px;top:61px;--n:56px;">
      <span class="num">25</span>
      <span class="suffix" style="margin-left:2px;"><span class="pct">%</span><span class="off">OFF</span></span>
    </div>
    <div class="line" style="left:37px;top:113px;font-size:57px;">SPRING DETOX</div>
    <div class="line" style="left:36px;top:152px;font-size:154px;">SALE</div>
    <div class="line" style="left:31px;top:279px;font-size:58px;">Spring Cleanse</div>
    <div class="line" style="left:26px;top:328px;font-size:58px;">Summer Glow</div>
  </section>

  <!-- Post 9 -->
  <section class="tile midnight col-a row-5">
    <div class="price center-price" style="top:53px;--n:101px;">
      <span class="num">25</span>
      <span class="suffix"><span class="pct">%</span><span class="off">OFF</span></span>
    </div>
    <div class="line center" style="top:151px;font-size:58px;">MOTHER’S DAY</div>
    <div class="line center" style="top:194px;font-size:146px;">SALE</div>
    <div class="line center sans" style="top:318px;font-size:26px;font-weight:600;">Detox This Spring.</div>
    <div class="line center sans" style="top:349px;font-size:26px;font-weight:600;">Shine This Summer</div>
  </section>

  <!-- Post 10 -->
  <section class="tile cobalt col-b row-5">
    <div class="price" style="left:35px;top:40px;--n:96px;">
      <span class="num">25</span>
      <span class="suffix"><span class="pct">%</span><span class="off">OFF</span></span>
    </div>
    <div class="product-shot" role="img" aria-label="Four white supplement bottles in a staggered row" style="left:172px;top:29px;width:160px;height:96px;"></div>
    <div class="line" style="left:35px;top:126px;font-size:58px;">MOTHER’S DAY</div>
    <div class="line" style="left:33px;top:170px;font-size:161px;">SALE</div>
    <div class="line" style="left:35px;top:300px;font-size:61px;">Spring Detox</div>
    <div class="line" style="left:35px;top:360px;font-size:43px;">for a Summer Body</div>
  </section>

</main>
</body>
</html>
```